BrivoTerna. Lantern of the Steady Harvest. Business card

Professional business card for BrivoTerna (Lantern of the Steady Harvest)
My rationale: Strategy-> Execution-> Results-> Value that lead to the BrivoTerna name: We put the Lantern of the Steady Harvest.
We deliver value to our customers helping them at defining a good strategy (cyan arrow). 90% of well formulated strategies fail due to poor execution so we also consider strategical execution very important (green arrow). Due to the execution we obtain the results (blue arrow). Finally, the results provide feedback to redefine strategy, and the new strategy has to be executed and new results obtained providing new feedback and on and on. It's like a wheel that finally, must create corporate value: value for shareholders, staholders, employees, providers...-

Target Market(s)

CEOs and steering comitees , invewrnent funds

Industry/Entity Type

Business Consultant

Contact Information for Business Card

Teodoro Vinsquel
CEO & Founder
teodoro.vinsquel@brivoterna-example.com
Mobile: +34 655.803.912
www.brivoterna-example.com

Colors

Designer to choose colors to be used in the design.

Requirements
Nice to have
• Nice to hace the words: Strategy, execution, results
• Nice to vave the claim: Lantern of the Steady Harvest
• The three colors should be shown:
• cyan for STRATEGY
• green for EXECUTION
• blue for RESULTS
Should not have
• Complete black background

```html
<!DOCTYPE html>
<html lang="en">
<head>
<meta charset="utf-8">
<title>BrivoTerna – Business Card</title>
<link rel="stylesheet" href="https://fonts.googleapis.com/css2?family=Open+Sans:wght@400;600;700;800&display=swap">
<style>
  :root {
    --brand-blue: #0b3a9e;
    --brand-green: #8cc63f;
    --brand-cyan: #00aeef;
    --card-white: #ffffff;
    --page-bg: #e8eaee;
    --ink-grey: #3c3c46;
  }
  * { box-sizing: border-box; margin: 0; padding: 0; }
  html, body {
    width: 1200px; height: 960px; overflow: hidden;
    background: var(--page-bg);
    font-family: "Open Sans", Arial, sans-serif;
  }
  .canvas {
    position: relative; width: 1200px; height: 960px;
    display: flex; flex-direction: column; align-items: center; justify-content: center; gap: 50px;
  }
  .card {
    position: relative; width: 740px; height: 420px;
    background: var(--card-white);
    box-shadow: 0 6px 20px rgba(0,0,0,.12);
    overflow: hidden;
  }

  /* Front */
  .card--front { display: flex; flex-direction: column; align-items: center; justify-content: center; }
  .brand-name {
    color: var(--brand-blue); font-weight: 800; letter-spacing: -1px; line-height: 1;
  }
  .card--front .brand-name { font-size: 76px; margin-top: 10px; }
  .front-website {
    margin-top: 34px; color: var(--ink-grey); font-size: 17px; letter-spacing: 2px;
  }
  .front-website strong { color: var(--brand-blue); font-weight: 600; }

  /* Back */
  .card--back { display: flex; }
  .back-brand {
    width: 50%; display: flex; align-items: center; justify-content: center;
  }
  .back-brand .brand-name { font-size: 58px; }
  .back-details {
    position: relative; width: 50%; background: var(--brand-blue);
  }
  .person {
    position: absolute; left: 34px; top: 48px; display: flex; align-items: center; gap: 16px;
  }
  .person-icon { width: 52px; height: 52px; flex: none; }
  .person-name { color: var(--brand-green); font-weight: 700; font-size: 25px; line-height: 1.1; }
  .person-role { color: var(--card-white); font-size: 15px; margin-top: 2px; }

  .contact-ribbon {
    position: absolute; left: -22px; right: 0; height: 44px;
    display: flex; align-items: center; gap: 12px; padding-left: 44px;
    color: var(--card-white); font-size: 14px;
    clip-path: polygon(0 0, 100% 0, 100% 100%, 0 100%, 18px 50%);
  }
  .contact-ribbon--phone { top: 170px; background: var(--brand-cyan); }
  .contact-ribbon--email { top: 232px; background: var(--brand-green); }
  .contact-ribbon--web { top: 294px; background: var(--brand-cyan); }
  .contact-icon { width: 28px; height: 28px; flex: none; }
  .back-footer-band {
    position: absolute; left: 0; right: 0; bottom: 0; height: 48px;
    background: var(--brand-blue); border-top: 4px solid var(--brand-cyan);
  }
</style>
</head>
<body>
<main class="canvas">

  <section class="card card--front" aria-label="Business card front">
    <div class="brand-name">BrivoTerna</div>
    <p class="front-website">www.<strong>brivoterna-example</strong>.com</p>
  </section>

  <section class="card card--back" aria-label="Business card back">
    <div class="back-brand">
      <div class="brand-name">BrivoTerna</div>
    </div>
    <div class="back-details">
      <div class="person">
        <svg class="person-icon" viewBox="0 0 52 52" aria-hidden="true">
          <circle cx="26" cy="26" r="24" fill="none" stroke="#8cc63f" stroke-width="2.5"/>
          <circle cx="26" cy="20" r="7" fill="#8cc63f"/>
          <path d="M13 38c0-7 6-11 13-11s13 4 13 11z" fill="#8cc63f"/>
        </svg>
        <div>
          <div class="person-name">Teodoro Vinsquel</div>
          <div class="person-role">CEO &amp; Founder</div>
        </div>
      </div>

      <div class="contact-ribbon contact-ribbon--phone">
        <svg class="contact-icon" viewBox="0 0 28 28" aria-hidden="true">
          <circle cx="14" cy="14" r="12.5" fill="none" stroke="#fff" stroke-width="1.6"/>
          <rect x="10" y="7" width="8" height="14" rx="1.5" fill="none" stroke="#fff" stroke-width="1.5"/>
          <circle cx="14" cy="18.5" r="0.9" fill="#fff"/>
        </svg>
        <span>+34 655.803.912</span>
      </div>

      <div class="contact-ribbon contact-ribbon--email">
        <svg class="contact-icon" viewBox="0 0 28 28" aria-hidden="true">
          <circle cx="14" cy="14" r="12.5" fill="none" stroke="#fff" stroke-width="1.6"/>
          <rect x="8" y="9.5" width="12" height="9" fill="none" stroke="#fff" stroke-width="1.5"/>
          <path d="M8 9.5l6 5 6-5" fill="none" stroke="#fff" stroke-width="1.5"/>
        </svg>
        <span>teodoro.vinsquel@brivoterna-example.com</span>
      </div>

      <div class="contact-ribbon contact-ribbon--web">
        <svg class="contact-icon" viewBox="0 0 28 28" aria-hidden="true">
          <circle cx="14" cy="14" r="12.5" fill="none" stroke="#fff" stroke-width="1.6"/>
          <circle cx="14" cy="14" r="6.5" fill="none" stroke="#fff" stroke-width="1.3"/>
          <ellipse cx="14" cy="14" rx="3" ry="6.5" fill="none" stroke="#fff" stroke-width="1.1"/>
          <path d="M7.5 14h13" stroke="#fff" stroke-width="1.1"/>
        </svg>
        <span>www.brivoterna-example.com</span>
      </div>

      <div class="back-footer-band"></div>
    </div>
  </section>

</main>
</body>
</html>
```